Business Card Design Project

We are not a new company, but renamed to "Vantorin Kitchens" last year. We specialize in modern high-end cabinetry imports. We would like to communicate a sense of quality and cutting edge technology. Ideally the design would incorporate our logo colors, silver, red and preferably a black, matte background. Though we are open to suggestions.
Logo is attached.
Edit: I have attached rough drafts of the previous cards, this way you will have all necessary content that needs to go on the cards.
Updates
Project Deadline Extended
Reason: We have received a lot of great designs, but due to the sheer number we couldn't respond to all. We will extend the deadline for another 7 days to finalize and provide feedback to designers.
Thank you for your hard work!
Industry/Entity Type
Business
Look and feel
Each slider illustrates characteristics of the customer's brand and the style your logo design should communicate.

```html
<!DOCTYPE html>
<html lang="en">
<head>
<meta charset="utf-8">
<title>Vantorin Kitchens – Business Cards</title>
<link href="https://fonts.googleapis.com/css2?family=PT+Sans:wght@400;700&family=PT+Sans+Narrow:wght@700&display=swap" rel="stylesheet">
<style>
  :root {
    --stage: #e4e4e2;
    --card-top: #2b2c2e;
    --card-bottom: #141516;
    --card-black: #050505;
    --silver: #c9cacc;
    --silver-light: #f0f0f0;
    --silver-dark: #8e8f91;
    --red: #e0242b;
    --text: #ffffff;
    --muted: #8a8b8d;
  }
  * { box-sizing: border-box; margin: 0; padding: 0; }
  html, body { width: 1200px; height: 788px; overflow: hidden; }
  body {
    background: var(--stage);
    position: relative;
    font-family: "PT Sans", Arial, sans-serif;
    color: var(--text);
  }
  .card {
    position: absolute;
    width: 525px;
    height: 299px;
    border-radius: 18px;
    overflow: hidden;
    background: linear-gradient(180deg, var(--card-top), var(--card-bottom));
    box-shadow: 0 6px 14px rgba(0,0,0,.35);
  }
  .card--front   { left: 50px;  top: 63px; }
  .card--front-2 { left: 625px; top: 63px; }
  .card--back    { left: 56px;  top: 447px; }
  .card--back-2  { left: 625px; top: 447px; background: var(--card-black); }

  .brand-mark {
    position: absolute;
    width: 40px; height: 40px;
    background: linear-gradient(180deg, var(--silver-light), var(--silver-dark));
  }
  .brand-name {
    position: absolute;
    font-weight: 700;
    text-transform: uppercase;
    color: var(--silver);
    white-space: nowrap;
    letter-spacing: 2px;
  }

  /* front */
  .card--front .brand-mark, .card--front-2 .brand-mark { left: 248px; top: 22px; }
  .band-red {
    position: absolute; left: 0; top: 88px; width: 57px; height: 27px;
    background: var(--red);
  }
  .band-silver {
    position: absolute; right: 0; top: 88px; width: 147px; height: 27px;
    background: linear-gradient(90deg, var(--silver-dark), var(--silver-light));
  }
  .card--front .brand-name, .card--front-2 .brand-name {
    left: 64px; top: 86px; font-size: 25px; line-height: 30px;
  }
  .person { position: absolute; left: 64px; top: 133px; }
  .person__name { font-size: 17px; line-height: 20px; letter-spacing: .3px; }
  .person__title {
    font-family: "PT Sans Narrow", "Arial Narrow", sans-serif;
    font-weight: 700; font-size: 10px; line-height: 14px; text-transform: uppercase;
  }
  .contact { position: absolute; left: 64px; top: 181px; list-style: none; }
  .contact li {
    display: flex; align-items: center;
    height: 19.5px; font-size: 12px;
  }
  .contact svg { width: 12px; height: 12px; margin-right: 17px; fill: var(--muted); }

  /* back */
  .card--back .brand-mark { left: 242px; top: 96px; }
  .card--back .brand-name { left: 0; right: 0; text-align: center; top: 160px; font-size: 27px; }
  .card--back-2 .brand-mark { left: 248px; top: 104px; }
  .card--back-2 .brand-name { left: 0; right: 0; text-align: center; top: 168px; font-size: 30px; }

  .perforation { position: absolute; }
  .perforation--top {
    left: 0; top: 0; width: 290px; height: 90px;
    background: radial-gradient(ellipse at 60% 40%, #3a3a3b 0%, #161617 55%, transparent 80%);
  }
  .perforation--bottom {
    right: 0; bottom: 0; width: 290px; height: 95px;
    background: radial-gradient(ellipse at 40% 60%, #3a3a3b 0%, #161617 55%, transparent 80%);
  }
</style>
</head>
<body>
  <svg width="0" height="0" style="position:absolute">
    <defs>
      <symbol id="i-phone" viewBox="0 0 12 12"><path d="M3 1l2 2.5-1.2 1.2a6 6 0 0 0 3.5 3.5L8.5 7 11 9l-1.3 1.8C5.5 10.8 1.2 6.5 1.2 2.3z"/></symbol>
      <symbol id="i-fax" viewBox="0 0 12 12"><rect x="3" y="1" width="6" height="4"/><rect x="1" y="5" width="10" height="5" rx="1"/></symbol>
      <symbol id="i-mobile" viewBox="0 0 12 12"><rect x="3.5" y="0.5" width="5" height="11" rx="1"/></symbol>
      <symbol id="i-mail" viewBox="0 0 12 12"><path d="M1 3h10v7H1z M1 3l5 4 5-4" /></symbol>
      <symbol id="i-home" viewBox="0 0 12 12"><path d="M6 1l5 5H9.5v5h-7V6H1z"/></symbol>
    </defs>
  </svg>

  <section class="card card--front">
    <div class="brand-mark"></div>
    <div class="band-red"></div>
    <div class="band-silver"></div>
    <div class="brand-name">Vantorin Kitchens</div>
    <div class="person">
      <p class="person__name">MAREK DOVAN</p>
      <p class="person__title">President</p>
    </div>
    <ul class="contact">
      <li><svg><use href="#i-phone"/></svg>555.201.4830</li>
      <li><svg><use href="#i-fax"/></svg>555.201.4831</li>
      <li><svg><use href="#i-mobile"/></svg>555.318.7742</li>
      <li><svg><use href="#i-mail"/></svg>marek@vantorinkitchens.ca</li>
      <li><svg><use href="#i-home"/></svg>2180 - 48 Ave., Calder, ON K2P 4R9</li>
    </ul>
  </section>

  <section class="card card--front-2">
    <div class="brand-mark"></div>
    <div class="band-red"></div>
    <div class="band-silver"></div>
    <div class="brand-name">Vantorin Kitchens</div>
    <div class="person">
      <p class="person__name">OSKAR DOVAN</p>
      <p class="person__title">Director</p>
    </div>
    <ul class="contact">
      <li><svg><use href="#i-phone"/></svg>555.201.4830</li>
      <li><svg><use href="#i-fax"/></svg>555.201.4831</li>
      <li><svg><use href="#i-mobile"/></svg>555.364.2915</li>
      <li><svg><use href="#i-mail"/></svg>oskar@vantorinkitchens.ca</li>
      <li><svg><use href="#i-home"/></svg>2180 - 48 Ave., Calder, ON K2P 4R9</li>
    </ul>
  </section>

  <section class="card card--back">
    <div class="brand-mark"></div>
    <div class="brand-name">Vantorin Kitchens</div>
  </section>

  <section class="card card--back-2">
    <div class="perforation perforation--top" role="img" aria-label="Perforated metal dot texture"></div>
    <div class="perforation perforation--bottom" role="img" aria-label="Perforated metal dot texture"></div>
    <div class="brand-mark"></div>
    <div class="brand-name">Vantorin Kitchens</div>
  </section>
</body>
</html>
```